IT Management and Consulting company wants a design

The website should transfer an innovative, forward-oriented, optimistic, and serious image to my customer. Because we work in an agile, the design should transfer this approach.

The new color should make a serious, but not boring, impression for the business visitors of top-level companies.

The main focus topics are:
* IT strategy consulting
* Digital transformation
* IT quality management

The website should be in the English language.

The website should be created for WordPress. The existing website is http://www.v-tek.com (no WordPress) is provided by servplanet.de. A WordPress sandbox system exists.

Target Market(s)

Purchasing departments, IT decision makers from companies, project recruiting companies

Industry/Entity Type

IT-Provider, Telecommunication, Automotive

Number of Pages Required

4 page

Font styles to use
Serif
Sans Serif

Requirements
Must have
• Long-pager scrolling, a detail page for each portfolio topics, contact page, page about the company
Nice to have
• Parallax animation less is more, maybe a nice Hero Video Header, interessting 3D graph, Isometric graphs will bi nice, more clean than overloaded,
Should not have
• personal recruting page like in www.v-tek.com

```html
<!DOCTYPE html>
<html lang="en">
<head>
<meta charset="utf-8">
<title>Vertek Consulting</title>
<link href="https://fonts.googleapis.com/css2?family=Noto+Serif:wght@400;700&family=Roboto:wght@400;500&display=swap" rel="stylesheet">
<style>
:root{
  --gold:#b9850c;
  --gold-cta:#bd8a12;
  --ink:#1d1d1d;
  --body:#3a3a3a;
  --white:#ffffff;
  --mist:#e9eaec;
  --navy:#1d3650;
  --black:#050505;
  --line:#a8a8a8;
}
*{margin:0;padding:0;box-sizing:border-box}
html,body{width:1200px;height:3738px;overflow:hidden}
body{position:relative;font-family:"Roboto",sans-serif;color:var(--body);background:var(--white)}
.abs{position:absolute}
.serif{font-family:"Noto Serif",serif}
.center{left:0;width:1200px;text-align:center}

/* hero */
.hero{top:0;left:0;width:1200px;height:618px;background:linear-gradient(110deg,#56636f 0%,#2c3440 35%,#3b3f48 60%,#1c1e22 100%)}
.hero-shade{top:0;left:0;width:1200px;height:618px;background:rgba(0,0,0,.3)}
.brand{left:112px;top:32px;color:var(--white);display:flex;align-items:center;gap:14px}
.brand-dot{width:14px;height:14px;border:2px solid var(--white);border-radius:50%}
.brand-name{font-family:"Roboto",sans-serif;font-size:25px;font-weight:400;line-height:1}
.nav{top:37px;left:463px;font-family:"Noto Serif",serif;font-size:15px;color:var(--white)}
.nav a{position:absolute;white-space:nowrap;color:var(--white);text-decoration:none}
.nav .active::after{content:"";position:absolute;left:3px;bottom:-12px;width:28px;height:3px;background:var(--white)}
.btn-touch{left:910px;top:26px;width:178px;height:38px;border:1.5px solid var(--white);border-radius:20px;color:var(--white);font-family:"Noto Serif",serif;font-size:14px;display:flex;align-items:center;justify-content:center;gap:10px}
.hero-title{top:205px;font-size:44px;color:var(--white);font-weight:400}
.hero-text{top:273px;left:282px;width:636px;text-align:center;font-size:15px;line-height:30px;color:var(--white)}
.btn{display:flex;align-items:center;justify-content:center;border-radius:24px;font-family:"Noto Serif",serif;font-size:16px}
.btn-light{border:1.5px solid var(--white);color:var(--white)}
.btn-gold{border:1.5px solid var(--gold);color:var(--gold)}
.ctrl{width:32px;height:32px;border-radius:50%;top:528px}

/* headings */
.eyebrow{font-size:15px;color:var(--gold)}
.h2{font-family:"Noto Serif",serif;font-size:38px;color:var(--ink);font-weight:400}
.rule{width:84px;height:3px;left:559px;background:linear-gradient(90deg,var(--gold) 50%,var(--line) 50%)}

/* cards */
.card{width:311px;height:297px;overflow:hidden}
.card-label{position:absolute;left:0;width:100%;text-align:center;font-family:"Noto Serif",serif;font-size:20px;color:var(--white)}
.card-panel{position:absolute;left:0;bottom:0;width:100%;height:71px;background:var(--gold);color:var(--white);font-size:14px;line-height:26px;text-align:center;padding-top:10px}

.mission{top:1184px;left:0;width:1200px;height:450px;background:linear-gradient(180deg,#eceef0,#e3e5e8)}
.mission-text{top:1378px;left:196px;width:808px;text-align:center;font-size:15px;line-height:30.5px;color:var(--body)}

.clients{top:1634px;left:0;width:1200px;height:554px;background:linear-gradient(120deg,#1f3a55 0%,#2a4a66 45%,#1a3149 100%)}
.quote{top:1926px;left:258px;width:684px;text-align:center;font-size:15px;line-height:31px;color:#e6ebf0;font-style:italic}
.badge{left:543px;top:2055px;width:114px;height:26px;background:var(--gold);color:var(--white);font-size:14px;display:flex;align-items:center;justify-content:center}

.blogs{top:2188px;left:0;width:1200px;height:678px;background:#ebecee}
.blog-text{top:2376px;left:276px;width:648px;text-align:center;font-size:15px;line-height:31px}
.blog-title{position:absolute;left:18px;font-family:"Noto Serif",serif;font-size:19px;line-height:30px;color:var(--white)}
.blog-date{position:absolute;left:18px;font-size:15px;color:var(--white)}

.cta{top:2866px;left:0;width:1200px;height:399px;background:var(--gold-cta)}
.cta-text{top:3020px;left:230px;width:740px;text-align:center;font-size:15px;line-height:31px;color:var(--white)}

.footer{top:3265px;left:0;width:1200px;height:473px;background:var(--black)}
.f-icon{width:78px;height:78px;border:2px solid var(--gold);border-radius:50%;top:3335px;display:flex;align-items:center;justify-content:center}
.f-label{top:3426px;width:260px;text-align:center;font-size:15px;font-weight:500;color:var(--white)}
.f-value{top:3455px;width:260px;text-align:center;font-size:13px;line-height:26px;color:var(--white)}
.f-rule{top:3536px;left:112px;width:976px;height:1px;background:#2a2a2a}
.social{width:52px;height:52px;border-radius:50%;border:1.5px solid #555;top:3586px}
.copy{top:3674px;font-size:14px;color:var(--white)}
</style>
</head>
<body>

<!-- Hero -->
<div class="abs hero" role="img" aria-label="Hero video still: consultant in a suit presenting to clients at a meeting table with a tablet"></div>
<div class="abs hero-shade"></div>
<div class="abs brand">
  <span class="brand-dot"></span>
  <div class="brand-name">Vertek Consulting</div>
</div>
<nav class="abs nav">
  <a class="active" style="left:0">Home</a>
  <a style="left:70px">Companies</a>
  <a style="left:177px">Portfolio</a>
  <a style="left:265px">Scouting</a>
  <a style="left:354px">Contact</a>
</nav>
<div class="abs btn-touch">
  <svg width="16" height="14" viewBox="0 0 16 14"><path d="M0 6 16 0 12 14 8 9 14 2 6 8Z" fill="#fff"/></svg>
  GET IN TOUCH
</div>
<h1 class="abs center hero-title serif">Vertek Consulting</h1>
<p class="abs hero-text">A deliberately high standard for which we bundle all the qualities that are important to meet them. For example, in-depth methodological and IT competence</p>
<div class="abs btn btn-light" style="left:524px;top:358px;width:152px;height:44px">Learn More</div>
<div class="abs ctrl" style="left:564px;background:var(--white)">
  <svg width="32" height="32" viewBox="0 0 32 32"><path d="M10 13h3l4-3v12l-4-3h-3z" fill="#222"/><path d="M19 13q2 3 0 6" stroke="#222" stroke-width="1.5" fill="none"/></svg>
</div>
<div class="abs ctrl" style="left:604px;background:var(--gold)">
  <svg width="32" height="32" viewBox="0 0 32 32"><rect x="11" y="10" width="3.5" height="12" fill="#fff"/><rect x="17.5" y="10" width="3.5" height="12" fill="#fff"/></svg>
</div>

<!-- Focus areas -->
<div class="abs center eyebrow" style="top:700px">Our services</div>
<h2 class="abs center h2" style="top:720px">Our Focus Areas</h2>
<div class="abs rule" style="top:780px"></div>

<div class="abs card" style="left:112px;top:801px;background:linear-gradient(135deg,#3c3f5a,#1e2338 60%,#2b3146)" role="img" aria-label="Business team reviewing charts on a laptop">
  <div class="card-label" style="top:133px">IT Strategy Consulting</div>
</div>
<div class="abs card" style="left:444px;top:801px;background:linear-gradient(160deg,#35557e,#15263d 70%)" role="img" aria-label="Hands using a smartphone next to a laptop">
  <svg class="abs" style="left:126px;top:128px" width="58" height="58" viewBox="0 0 58 58"><circle cx="29" cy="29" r="29" fill="#fff"/><circle cx="29" cy="29" r="11" fill="none" stroke="var(--gold)" stroke-width="2"/><circle cx="29" cy="29" r="4" fill="none" stroke="var(--gold)" stroke-width="2"/><path d="M29 14v4M29 40v4M14 29h4M40 29h4M18.5 18.5l3 3M36.5 36.5l3 3M18.5 39.5l3-3M36.5 21.5l3-3" stroke="var(--gold)" stroke-width="2.5"/></svg>
  <div class="card-panel">Lorem ipsum dolor sit amet, consecte-<br>tur adipiscing elit, sed do eiusmod</div>
</div>
<div class="abs card" style="left:776px;top:801px;background:linear-gradient(135deg,#5a4436,#2a2622 55%,#3b2f2a)" role="img" aria-label="Professional woman working on a tablet in an office">
  <div class="card-label" style="top:133px">IT quality management</div>
</div>

<!-- Mission -->
<div class="abs mission" role="img" aria-label="Faint background of a person working on a laptop"></div>
<div class="abs center eyebrow" style="top:1277px">Our Mission</div>
<h2 class="abs center h2" style="top:1297px">Mission And Vision</h2>
<div class="abs rule" style="top:1356px"></div>
<p class="abs mission-text">A deliberately high standard for which we bundle all the qualities that are important to meet them. For example, in-depth methodological and IT competence as well as many years of experience in projects throughout the entire de-velopment process - supplemented by the ability to constructively involve all those involved.</p>
<div class="abs btn btn-gold" style="left:535px;top:1492px;width:151px;height:45px">Learn More</div>

<!-- Testimonials -->
<div class="abs clients" role="img" aria-label="Dark blue background of hands on a laptop with gear and chart graphics"></div>
<div class="abs center eyebrow" style="top:1719px">People</div>
<h2 class="abs center h2" style="top:1744px;color:var(--white)">What Do Clients Say?</h2>
<div class="abs" style="left:565px;top:1842px;width:70px;height:70px;border-radius:50%;border:3px solid var(--white);background:linear-gradient(#b8b0a8,#6d625a)" role="img" aria-label="Client portrait"></div>
<p class="abs quote">Lorem ipsum dolor sit amet, consectetur adipiscing elit, sed do eiusmod tempor incididunt ut labore et dolore magna aliqua. Quis ipsum suspendisse ultrices gravida.</p>
<div class="abs center serif" style="top:2016px;font-size:16px;color:var(--white)">Morgan Ellery</div>
<div class="abs badge">Lorem Ipsum</div>
<svg class="abs" style="left:180px;top:1938px" width="22" height="42" viewBox="0 0 22 42"><path d="M20 2 2 21l18 19" stroke="#d8dde3" stroke-width="2" fill="none"/></svg>
<svg class="abs" style="left:998px;top:1938px" width="22" height="42" viewBox="0 0 22 42"><path d="M2 2l18 19L2 40" stroke="#d8dde3" stroke-width="2" fill="none"/></svg>

<!-- Blogs -->
<div class="abs blogs"></div>
<div class="abs center eyebrow" style="top:2274px;left:9px">News</div>
<h2 class="abs center h2" style="top:2294px;left:9px">Latest Blogs</h2>
<div class="abs rule" style="top:2353px;left:567px"></div>
<p class="abs blog-text">Lorem ipsum dolor sit amet, consectetur adipiscing elit, sed do eiusmod tempor incididunt ut labore et dolore magna aliqua. Quis ipsum suspendisse ultrices gravida.</p>

<div class="abs card" style="left:112px;top:2470px;height:296px;background:linear-gradient(135deg,#2b3036,#4a5058 55%,#283a4e)" role="img" aria-label="Developer working at multiple code screens">
  <div class="blog-title" style="top:190px">Lorem ipsum dolor sit<br>amet, consectetur</div>
  <div class="blog-date" style="top:260px">24 Sep 2021</div>
</div>
<div class="abs card" style="left:445px;top:2470px;height:296px;background:linear-gradient(135deg,#4a4440,#2f2c2b 60%,#45403c)" role="img" aria-label="Team meeting around a table with documents">
  <div class="blog-title" style="top:104px">Lorem ipsum dolor sit<br>amet, consectetur</div>
  <div class="blog-date" style="top:174px">24 Sep 2021</div>
  <div class="abs serif" style="left:20px;top:240px;font-size:15px;color:var(--gold);display:flex;align-items:center;gap:8px">Learn More
    <svg width="14" height="14" viewBox="0 0 14 14"><circle cx="7" cy="7" r="7" fill="var(--gold)"/><path d="M5.5 4 8.5 7 5.5 10" stroke="#fff" stroke-width="1.6" fill="none"/></svg></div>
</div>
<div class="abs card" style="left:778px;top:2470px;height:296px;background:linear-gradient(135deg,#6a5a48,#3a322c 55%,#5c4e40)" role="img" aria-label="Two colleagues discussing work at a laptop">
  <div class="blog-title" style="top:190px">Lorem ipsum dolor sit<br>amet, consectetur</div>
  <div class="blog-date" style="top:260px">24 Sep 2021</div>
</div>

<!-- CTA -->
<div class="abs cta"></div>
<h2 class="abs center h2" style="top:2956px;color:var(--white)">Ready To Get In Touch?</h2>
<p class="abs cta-text">Lorem ipsum dolor sit amet, consectetur adipiscing elit, sed do eiusmod tempor incididunt ut labore et dolore magna aliqua. Quis ipsum suspendisse ultrices gravida.</p>
<div class="abs btn btn-light" style="left:524px;top:3121px;width:151px;height:45px">Learn More</div>

<!-- Footer -->
<footer class="abs footer"></footer>
<div class="abs f-icon" style="left:266px">
  <svg width="14" height="22" viewBox="0 0 14 22"><rect x="1" y="1" width="12" height="20" rx="2" fill="none" stroke="#fff" stroke-width="2"/><circle cx="7" cy="17" r="1.3" fill="#fff"/></svg>
</div>
<div class="abs f-icon" style="left:546px">
  <svg width="16" height="22" viewBox="0 0 16 22"><path d="M8 21C3 14 1 11 1 8a7 7 0 0 1 14 0c0 3-2 6-7 13z" fill="#fff"/><circle cx="8" cy="8" r="2.6" fill="#050505"/></svg>
</div>
<div class="abs f-icon" style="left:833px">
  <svg width="22" height="16" viewBox="0 0 22 16"><rect width="22" height="16" rx="1" fill="#fff"/><path d="M1 1l10 8 10-8" stroke="#050505" stroke-width="1.8" fill="none"/></svg>
</div>
<div class="abs f-label" style="left:175px">PHONE</div>
<div class="abs f-value" style="left:175px">100-555-0142</div>
<div class="abs f-label" style="left:458px">ADDRESS</div>
<div class="abs f-value" style="left:458px">Lorem ipsum dolor sit amet,<br>consectetur</div>
<div class="abs f-label" style="left:742px">EMAIL</div>
<div class="abs f-value" style="left:742px">info@vertekconsulting</div>
<div class="abs f-rule"></div>
<div class="abs social" style="left:469px" aria-label="Social link"></div>
<div class="abs social" style="left:538px;background:var(--gold);border-color:var(--gold)" aria-label="Social link"></div>
<div class="abs social" style="left:608px" aria-label="Social link"></div>
<div class="abs social" style="left:679px" aria-label="Social link"></div>
<div class="abs center copy">©Copyrights 2021 Company Name &nbsp; | &nbsp; All Rights Reserved</div>

</body>
</html>
```